Profesional personal website needs design and business card

I need a business card with my professional name as a logo "Dorian Vitality" for my business. I am a Wellness Coach, consultant and trainer. So it should be professional, wellness oriented and modern.

Target Market(s)

Private clients, governments, corporations. Luxury and high market.

Industry/Entity Type

Health And Wellness

Contact Information for Business Card

Dorian Vitality should be the logo

Colors

Designer to choose colors to be used in the design.

Requirements
Must have
• Dorian Vitality
• Name: Tomás Lirandel
• Wellness Coach, Consultant & Trainer.
• Website: www.dorianvitality-example.com
• Phone:
• Spain (+34) 612 480 317
• (USA) +1 (555) 610 4829
Nice to have
• The most important is the design of "Dorian Vitality", as this is going to be my personal brand logo. It should be professional, wellness, high end and actual.
Should not have
• no golds, no baroque style..

```html
<!DOCTYPE html>
<html lang="en">
<head>
<meta charset="utf-8">
<title>Dorian Vitality — Business Card</title>
<link rel="stylesheet" href="https://fonts.googleapis.com/css2?family=Montserrat:wght@300;400;500;700&display=swap">
<style>
  :root {
    --backdrop: #efe6d8;
    --leaf-green: #8bc33f;
    --charcoal: #232325;
    --ink: #1f1f21;
    --white: #ffffff;
  }
  * { margin: 0; padding: 0; box-sizing: border-box; }
  html, body {
    width: 1200px;
    height: 1200px;
    overflow: hidden;
    background: var(--backdrop);
    font-family: "Montserrat", sans-serif;
  }
  .sheet {
    width: 1200px;
    height: 1200px;
    display: flex;
    flex-direction: column;
    align-items: center;
    justify-content: center;
    gap: 40px;
  }
  .card {
    position: relative;
    width: 840px;
    height: 538px;
    overflow: hidden;
    box-shadow: 0 10px 30px rgba(60, 45, 25, 0.18);
  }
  .card-front { background: var(--leaf-green); color: var(--white); }
  .card-back { background: var(--charcoal); }

  .holder-name {
    position: absolute;
    left: 52px;
    top: 50px;
    font-size: 40px;
    line-height: 1;
    letter-spacing: 3px;
    white-space: nowrap;
  }
  .holder-name .given { font-weight: 700; }
  .holder-name .family { font-weight: 300; }
  .holder-role {
    position: absolute;
    left: 52px;
    top: 95px;
    font-size: 14px;
    line-height: 1;
    font-weight: 400;
    letter-spacing: 2.4px;
    white-space: nowrap;
  }
  .divider {
    position: absolute;
    left: 0;
    top: 0;
  }
  .contact-line {
    position: absolute;
    left: 52px;
    display: flex;
    align-items: flex-start;
    gap: 28px;
    font-size: 21px;
    font-weight: 400;
    letter-spacing: 1.4px;
    line-height: 1.15;
  }
  .contact-web { top: 150px; }
  .contact-phone { top: 449px; }
  .contact-line svg { flex: none; margin-top: 3px; }

  .back-slash { position: absolute; left: 0; top: 0; }
  .brand-name {
    position: absolute;
    left: 390px;
    top: 240px;
    font-size: 44px;
    font-weight: 500;
    letter-spacing: 1px;
    color: var(--leaf-green);
    white-space: nowrap;
  }
</style>
</head>
<body>
<main class="sheet">

  <section class="card card-front" aria-label="Business card front">
    <h1 class="holder-name"><span class="given">TOMÁS</span> <span class="family">LIRANDEL</span></h1>
    <p class="holder-role">Wellness Coach - Consultant &amp; Trainer</p>

    <svg class="divider" width="840" height="538" viewBox="0 0 840 538" aria-hidden="true">
      <polyline points="0,128 670,128 670,141 840,141" fill="none" stroke="var(--ink)" stroke-width="3.5"/>
    </svg>

    <p class="contact-line contact-web">
      <svg width="14" height="20" viewBox="0 0 14 20" aria-hidden="true">
        <path d="M1 1 L1 16 L5 12 L8 19 L10.5 18 L7.5 11 L13 11 Z" fill="var(--white)"/>
      </svg>
      <span>www.dorianvitality-example.com</span>
    </p>

    <p class="contact-line contact-phone">
      <svg width="18" height="20" viewBox="0 0 18 20" aria-hidden="true">
        <path d="M4 1 L7 6 L5 8 C6 11 8 13.5 11 15 L13 13 L17 16 L15 19 C8 18.5 2 12 1.5 4 Z" fill="var(--white)"/>
      </svg>
      <span>SPAIN(+34) 612 480 317<br>USA &nbsp;+1 (555) 610 4829</span>
    </p>
  </section>

  <section class="card card-back" aria-label="Business card back">
    <svg class="back-slash" width="840" height="538" viewBox="0 0 840 538" aria-hidden="true">
      <line x1="618" y1="-4" x2="0" y2="544" stroke="var(--white)" stroke-width="7"/>
    </svg>
    <p class="brand-name">Dorian Vitality</p>
  </section>

</main>
</body>
</html>
```